Need flyer for honey

I need the advertising flyer for my honey products. Will need around 4-6 page A5 size. Flyer content is ready but will need to check the wording and need the artwork and pictures designed in a proper manner.

Advertising

```html
<!DOCTYPE html>
<html lang="en">
<head>
<meta charset="utf-8">
<title>Why Australian Honey – Flyer Page</title>
<link rel="stylesheet" href="https://fonts.googleapis.com/css2?family=Roboto:wght@400;500;700&display=swap">
<style>
  :root {
    --paper: #ffffff;
    --yellow: #fbe829;
    --ink: #2b2b2b;
    --body-grey: #6a6a6a;
    --box-ink: #3a3526;
    --hex-gap: #ffffff;
  }
  * { box-sizing: border-box; margin: 0; padding: 0; }
  html, body {
    width: 1200px; height: 849px; overflow: hidden;
    background: var(--paper);
  }
  .flyer {
    position: relative; width: 1200px; height: 849px;
    background: var(--paper);
    font-family: "Roboto", Arial, sans-serif;
    color: var(--body-grey);
    overflow: hidden;
  }
  .abs { position: absolute; }
  .title-bar {
    left: 44px; top: 78px; width: 476px; height: 46px;
    background: var(--yellow);
    display: flex; align-items: center; padding-left: 44px;
    font-size: 23px; font-weight: 400; color: var(--ink); letter-spacing: 0.3px;
  }
  .title-bar strong { font-weight: 700; margin: 0 6px; }
  .section-title {
    font-size: 19px; font-weight: 700; color: var(--ink);
    text-transform: uppercase; line-height: 1.1; margin-bottom: 3px;
  }
  .body-copy {
    font-size: 13.4px; line-height: 16.3px; text-align: justify;
  }
  .clean { left: 44px; top: 134px; width: 508px; }
  .eucalyptus-photo {
    left: 560px; top: 0; width: 92px; height: 217px;
    background: linear-gradient(160deg, #6f8a5c 0%, #8ea37a 40%, #e0407a 70%, #f5f5f3 100%);
    border-radius: 0 0 46px 46px;
  }
  .right-column { left: 667px; top: 70px; width: 456px; }
  .right-column .lead { margin-bottom: 10px; }
  .pure-box {
    left: 43px; top: 304px; width: 556px; height: 295px;
    background: var(--yellow);
    padding: 28px 50px 0 44px;
    color: var(--box-ink);
  }
  .pure-box .body-copy { color: var(--box-ink); }
  .pure-box p + p { margin-top: 6px; }
  .pure-box .narrow { width: 290px; text-align: left; }
  .honey-photo {
    left: 405px; top: 522px; width: 212px; height: 145px;
    background: radial-gradient(ellipse at 55% 45%, #f4b73a 0%, #e9a21f 35%, #f7e0a8 62%, rgba(255,255,255,0) 78%);
  }
  .taster-photo {
    left: 0; top: 623px; width: 165px; height: 226px;
    background: linear-gradient(180deg, #e9ddd6 0%, #d7b7a6 45%, #2a2a2a 100%);
  }
  .unique { left: 175px; top: 682px; width: 373px; }
  .unique .section-title { font-size: 17px; }
  .hex-grid { left: 0; top: 0; width: 1200px; height: 849px; pointer-events: none; }
</style>
</head>
<body>
<main class="flyer">

  <div class="abs eucalyptus-photo" role="img" aria-label="Eucalyptus branch with pink blossoms and green leaves"></div>

  <h1 class="abs title-bar">WHY <strong>AUSTRALIAN</strong> HONEY?</h1>

  <section class="abs clean">
    <h2 class="section-title">Clean &amp; Chemical Free</h2>
    <p class="body-copy">Unlike many other countries producing honey, Australia has miles of pristine native forests and diverse native flowers that are chemical free which provides the clean honey nectar resources. Meanwhile, the honey bee industry is well protected by the National Biosecurity Inspection Office which keeps industry free from varroa mite and other exotic diseases. Very rare the chemicals are used in diseases control. Therefore from the very original source, Australia honey is clean than from any other part of the world.</p>
  </section>

  <section class="abs right-column">
    <p class="body-copy lead">delivers various tastes from gentle sweetness and mild caramel like to noticeable fragrance and sweet. Out of which everyone can find a taste of his own.</p>
    <h2 class="section-title">Safety Assured</h2>
    <p class="body-copy">As a country prioritizes its people's health and safety, the Australia government and regulation bodies have established the world's most strict food safety standards. There are also strict quality control procedures in the honey &amp; bee industry that all apiarists and honey packers must adhere to. Therefore, Australia is the rare country in the world that has very low risk of contamination from honey collection to packing and to distribution.</p>
  </section>

  <section class="abs pure-box">
    <h2 class="section-title">Pure &amp; Healthy</h2>
    <p class="body-copy">Honey is healthy food, while many overseas honey producers are commercialized, who would minimize the honey production circle to enhance production and adulterate their honey to make it a common consistency. Color and flavor are controlled by adding additives, sugars, syrups and extenders.</p>
    <p class="body-copy">On the other hand, the Australian honey bee industry has a commitment to purity. Australian honey producers do not use any of the additives or sugars to make their honey better looking. Instead, they insist to make honey that is 100% pure and natural. Honey is left in the hives to let bee</p>
    <p class="body-copy narrow" style="margin-top:0">fan it until the water content drops to a certain level while the nutrition level is protected and raised.</p>
  </section>

  <div class="abs honey-photo" role="img" aria-label="Honeycomb piece and wooden honey dipper in a dish of honey with mint leaves"></div>

  <div class="abs taster-photo" role="img" aria-label="Woman in a black top tasting honey from her fingers"></div>

  <section class="abs unique">
    <h2 class="section-title">Unique Taste</h2>
    <p class="body-copy">Australia is home to more than ten thousand species of plants and flowers, many of which are found nowhere else in the world. The country's unique native Eucalyptus trees and flowers create distinctive flavors of honey. From dark amber to golden light in the color, Australia honey</p>
  </section>

  <svg class="abs hex-grid" viewBox="0 0 1200 849" xmlns="http://www.w3.org/2000/svg">
    <defs>
      <linearGradient id="tone-keeper" x1="0" y1="0" x2="0" y2="1">
        <stop offset="0" stop-color="#9fc16a"/>
        <stop offset="0.5" stop-color="#e8ece6"/>
        <stop offset="1" stop-color="#7d8a6a"/>
      </linearGradient>
      <linearGradient id="tone-comb" x1="0" y1="0" x2="1" y2="1">
        <stop offset="0" stop-color="#e0a23a"/>
        <stop offset="0.5" stop-color="#f3cf6a"/>
        <stop offset="1" stop-color="#8a5a22"/>
      </linearGradient>
      <linearGradient id="tone-frame" x1="0" y1="0" x2="0" y2="1">
        <stop offset="0" stop-color="#6f9a4c"/>
        <stop offset="0.45" stop-color="#e6e8e2"/>
        <stop offset="1" stop-color="#5a4a34"/>
      </linearGradient>
      <linearGradient id="tone-flower" x1="0" y1="0" x2="1" y2="1">
        <stop offset="0" stop-color="#2f7a1f"/>
        <stop offset="0.6" stop-color="#5aa52a"/>
        <stop offset="1" stop-color="#e5d21a"/>
      </linearGradient>
    </defs>
    <polygon role="img" aria-label="Beekeeper in protective suit holding a honeycomb frame"
      fill="url(#tone-keeper)" stroke="var(--hex-gap)" stroke-width="6"
      points="750,297 892,379 892,543 750,625 608,543 608,379"/>
    <polygon role="img" aria-label="Close-up of honey bees on capped honeycomb"
      fill="url(#tone-comb)" stroke="var(--hex-gap)" stroke-width="6"
      points="1048,297 1190,379 1190,543 1048,625 906,543 906,379"/>
    <polygon role="img" aria-label="Beekeeper inspecting a hive frame covered in bees"
      fill="url(#tone-frame)" stroke="var(--hex-gap)" stroke-width="6"
      points="899,540 1041,622 1041,786 899,868 757,786 757,622"/>
    <polygon role="img" aria-label="Bee collecting nectar on yellow flowers"
      fill="url(#tone-flower)" stroke="var(--hex-gap)" stroke-width="6"
      points="1197,540 1339,622 1339,786 1197,868 1055,786 1055,622"/>
  </svg>

</main>
</body>
</html>
```